Quanbrook Limited needs a business card design

We need a business card design that reflects both professionalism and innovation and captures our brand identity. We provide online enterprise solutions to HR and executive management. We would like to use the colors in our logo (Blue and Orange). See attached file.

We would like a more creative design than the existing attached business card but maintain the same information on it.

To see our products site, please visit www.quanbrook.example which reflects more our identity
Updates

Please see our site: www.quanbrook.example, not www.quanbrook.example.uk for our colors and look and feel

Target Market(s)

Senior Executives

Industry/Entity Type

Business

Requirements
Must have
• Logo and use of logo colors
Nice to have
• Icons
Should not have
• Images

```html
<!DOCTYPE html>
<html lang="en">
<head>
<meta charset="utf-8">
<title>Quanbrook Limited – Business Card</title>
<link rel="stylesheet" href="https://fonts.googleapis.com/css2?family=Questrial&display=swap">
<style>
  :root {
    --page-bg: #eeeeec;
    --card-bg: #ffffff;
    --brand-blue: #1c6fb8;
    --brand-orange: #ee7c2e;
    --deco-blue: #c6dcf0;
    --deco-peach: #f4c7ab;
    --text-grey: #5a5a5a;
    --text-light: #8a8a8a;
  }
  * { box-sizing: border-box; margin: 0; padding: 0; }
  html, body {
    width: 1200px; height: 1184px; overflow: hidden;
    background: var(--page-bg);
    font-family: "Questrial", "Century Gothic", sans-serif;
  }
  .canvas {
    position: relative; width: 1200px; height: 1184px;
    display: flex; flex-direction: column; align-items: center;
    justify-content: space-evenly;
  }
  .card {
    position: relative; width: 960px; height: 533px;
    background: var(--card-bg); overflow: hidden;
    box-shadow: 0 6px 20px rgba(0,0,0,0.12);
  }
  .deco-word {
    position: absolute; color: var(--deco-blue);
    font-weight: 400; line-height: 1; letter-spacing: -0.03em;
    white-space: nowrap; user-select: none;
  }

  /* Front */
  .card-front .brand-name {
    position: absolute; left: 56px; top: 64px;
    font-size: 46px; color: var(--brand-blue);
  }
  .card-front .deco-word { left: 480px; top: -58px; font-size: 240px; }
  .card-front .company {
    position: absolute; left: 0; right: 0; top: 300px; text-align: center;
    font-size: 42px; font-weight: 400; color: var(--brand-orange);
  }
  .card-front .tagline {
    position: absolute; left: 0; right: 0; top: 366px; text-align: center;
    font-size: 20px; letter-spacing: 0.08em; color: var(--text-grey);
  }
  .card-front .legal {
    position: absolute; left: 0; right: 0; top: 418px; text-align: center;
    font-size: 13px; line-height: 1.9; color: var(--text-light);
  }

  /* Back */
  .card-back .deco-word { left: -60px; bottom: -48px; font-size: 230px; }
  .card-back .deco-dot {
    position: absolute; left: 470px; top: 238px;
    width: 62px; height: 62px; border-radius: 50%; background: var(--deco-peach);
  }
  .card-back .person { position: absolute; left: 150px; top: 110px; }
  .card-back .person-name { font-size: 32px; letter-spacing: 0.01em; }
  .card-back .first { color: var(--brand-blue); }
  .card-back .last { color: var(--brand-orange); }
  .card-back .role {
    font-size: 16px; letter-spacing: 0.14em; color: var(--text-grey); margin-top: 2px;
  }
  .card-back .details {
    position: absolute; left: 620px; top: 70px;
    font-size: 17px; line-height: 1.5; color: var(--text-grey);
  }
  .card-back .address { margin-bottom: 56px; }
  .contact-row { display: flex; }
  .contact-label { width: 40px; color: var(--brand-blue); }
  .contact-group { margin-bottom: 12px; }
</style>
</head>
<body>
<main class="canvas">
  <section class="card card-front" aria-label="Business card front">
    <div class="deco-word" aria-hidden="true">Quan</div>
    <div class="brand-name">Quanbrook</div>
    <h1 class="company">Quanbrook Limited</h1>
    <p class="tagline">DEVELOPING LEADERS AND ORGANISATIONS</p>
    <p class="legal">Quanbrook Limited is a company registered in England &amp; Wales with company number 01234567<br>
      Registered Office: Mill House, Fenwick Road, Ashcombe, Surrey, AB12 3CD</p>
  </section>

  <section class="card card-back" aria-label="Business card back">
    <div class="deco-word" aria-hidden="true">brook</div>
    <div class="deco-dot" aria-hidden="true"></div>
    <div class="person">
      <div class="person-name"><span class="first">NADIA</span><span class="last">KERVANI</span></div>
      <div class="role">MANAGING DIRECTOR</div>
    </div>
    <div class="details">
      <p class="address">quanbrook limited<br>1208 Alder Court,<br>45 Marlow St, London, E1A 2ZZ</p>
      <div class="contact-group contact-row">
        <span class="contact-label">T.</span>
        <span>+44 20 5550 1423<br>+1 323 555 0187<br>+96170 555012</span>
      </div>
      <div class="contact-group contact-row">
        <span class="contact-label">E.</span><span>nkervani@quanbrook.example.uk</span>
      </div>
      <div class="contact-row">
        <span class="contact-label">W.</span><span>www.quanbrook.example.uk</span>
      </div>
    </div>
  </section>
</main>
</body>
</html>
```